vorne matcha

I'm a local business called 'VORNE' and will be sourcing organic ceremonial grade matcha tea through a private labeler in Japan. I need a sleek layout for the label that wraps around the tin that holds the 30g of matcha. I have samples of inspiration and designs that I like. This is very high end matcha so I would like for it to have an expensive look. I also have the dimensions of the label for the tin to show. I have specifics of things that need to be on the label, so please let me know if you need any of that information at this point!

Target Market(s)

High end matcha tea drinkers. The label files I sent are what my eye was drawn to.

Industry/Entity Type

matcha

Font styles to use
Other font styles liked:
• I like the font styles of the samples I uploaded in the photos

Colors

Designer to choose only greyscale colors for use in the design.

Requirements
Must have
• In the biggest lettering of them all in the center is MATCHA. (everything capitalized).Above it, my brand name which is VORNE. and if it looks good, Vorne no.7 like the Duvelle no.5.below the MATCHA, I would like it to say Ceremonial Grade.Another thing... Design wise!I would like the tin to be silver, and the label to be a sort of creme, in between white color with black lettering. Also, I would like the font to be more along the lines of the Ma Verte fonts I sent you... the files that show the cologne bottle with the silver top, creme label, and lettering:)Thanks so much and can't to see what you doOn it as well, the USDA certified organic label, which is in one of the screenshots I uploaded.There needs to be the net weight which is 30g. and also that it is sourced in Uji, Japanmy website on the back: www.saptamatcha.comThe nutrition facts and how to use I will send later:)
Nice to have
• my signature somewhere (like the coffee picture I sent)

```html
<!DOCTYPE html>
<html lang="en">
<head>
<meta charset="utf-8">
<title>Vorne Matcha – Tin Label Options</title>
<link rel="stylesheet" href="https://fonts.googleapis.com/css2?family=Archivo:wght@400;800&family=IBM+Plex+Mono:wght@400;600;700&family=Libre+Caslon+Text:wght@400;700&family=Noto+Serif+JP:wght@500&family=Oswald:wght@300;700&display=swap">
<style>
  :root {
    --page: #ffffff;
    --label: #fdfdfc;
    --ink: #333333;
    --ink-soft: #555555;
    --rule: #4a4a4a;
    --placeholder: #d9d9d9;
    --shadow: rgba(0, 0, 0, 0.32);
  }
  * { box-sizing: border-box; margin: 0; padding: 0; }
  html, body {
    width: 1200px; height: 1001px; overflow: hidden;
    background: var(--page); color: var(--ink);
    font-family: "IBM Plex Mono", monospace;
  }
  .sheet { position: relative; width: 1200px; height: 1001px; }

  .label {
    position: absolute; left: 50px; width: 1100px; height: 236px;
    background: var(--label);
    box-shadow: 0 0 3px rgba(0,0,0,.35), 0 26px 30px -18px var(--shadow);
  }
  .label--one   { top: 60px; }
  .label--two   { top: 382px; }
  .label--three { top: 704px; }

  .signature {
    position: absolute; left: 92px; top: 64px; width: 26px; height: 104px;
    background: var(--placeholder); border-radius: 13px;
  }
  .website {
    position: absolute; left: 150px; top: 56px;
    font-size: 9px; letter-spacing: .2px;
  }
  .badge-usda {
    position: absolute; left: 150px; top: 82px; width: 46px; height: 46px;
    border-radius: 50%; background: var(--ink);
    box-shadow: inset 0 0 0 4px var(--label), inset 0 0 0 6px var(--ink);
  }
  .badge-jas {
    position: absolute; left: 208px; top: 86px; width: 60px; height: 38px;
    border-radius: 50%; border: 2px solid var(--ink);
  }
  .source-box {
    position: absolute; left: 143px; top: 134px; width: 126px; height: 32px;
    border: 1px solid var(--ink);
    font-size: 9px; line-height: 12px; padding: 3px 0 0 22px;
  }
  .source-box .map {
    position: absolute; right: 10px; top: 5px; width: 16px; height: 20px;
    background: var(--ink-soft); border-radius: 3px;
  }
  .net-weight {
    position: absolute; left: 146px; top: 175px;
    font-size: 11px; font-weight: 700; letter-spacing: 1px;
  }
  .tagline-jp {
    position: absolute; left: 340px; top: 74px;
    writing-mode: vertical-rl; font-family: "Noto Serif JP", serif;
    font-size: 12px; letter-spacing: 2px;
  }

  .title-block {
    position: absolute; left: 384px; top: 66px; width: 246px; text-align: center;
  }
  .brand-line { font-size: 13px; letter-spacing: 3px; }
  .product-name { line-height: 1; margin-top: 2px; }
  .rule { height: 1px; background: var(--rule); margin: 4px 0 7px; }
  .grade {
    font-family: "IBM Plex Mono", monospace; font-weight: 600;
    font-size: 17px; letter-spacing: 1.5px;
  }

  .label--one .brand-line { font-family: "Oswald", sans-serif; font-weight: 700; font-size: 14px; }
  .label--one .product-name { font-family: "Oswald", sans-serif; font-weight: 700; font-size: 54px; letter-spacing: 5px; transform: scaleY(1.05); }

  .label--two .brand-line { font-family: "Archivo", sans-serif; font-weight: 400; font-size: 16px; }
  .label--two .product-name { font-family: "Archivo", sans-serif; font-weight: 800; font-size: 50px; letter-spacing: 1px; }

  .label--three .brand-line { font-family: "Libre Caslon Text", serif; font-weight: 400; font-size: 16px; }
  .label--three .product-name { font-family: "Libre Caslon Text", serif; font-weight: 700; font-size: 44px; letter-spacing: 1px; margin-top: 6px; }

  .info-box {
    position: absolute; left: 698px; width: 288px;
    border: 1px solid var(--ink); padding: 3px 10px 4px;
  }
  .info-box--ingredients { top: 44px; height: 58px; }
  .info-box--usage { top: 114px; height: 82px; }
  .info-box h3 {
    font-size: 7px; font-weight: 700; letter-spacing: .5px;
    padding-bottom: 2px; border-bottom: 1px dashed var(--ink); margin: 0 -10px 4px; padding-left: 10px;
  }
  .info-box p { font-size: 7.6px; line-height: 10.6px; text-align: justify; }
</style>
</head>
<body>
<main class="sheet">

  <section class="label label--one">
    <div class="signature" role="img" aria-label="Owner's handwritten signature"></div>
    <p class="website">www.vornematcha.com</p>
    <div class="badge-usda" role="img" aria-label="Organic certification badge"></div>
    <div class="badge-jas" role="img" aria-label="Japanese organic certification badge"></div>
    <div class="source-box">Sourced in<br>Uji, Japan<span class="map" role="img" aria-label="Outline map of Japan"></span></div>
    <p class="net-weight">NET WEIGHT: 30G</p>
    <p class="tagline-jp">生まれ変わった</p>
    <div class="title-block">
      <p class="brand-line">VORNE NO.7</p>
      <h1 class="product-name">MATCHA</h1>
      <div class="rule"></div>
      <p class="grade">CEREMONIAL GRADE</p>
    </div>
    <div class="info-box info-box--ingredients">
      <h3>INGREDIENTS:</h3>
      <p>Lorem ipsum dolor sit amet, consectetuer adipiscing elit, sed diam nonummy nibh euismod tincidunt ut laoreet dolore magna aliquam erat volutpat. Ut wisi</p>
    </div>
    <div class="info-box info-box--usage">
      <h3>HOW TO USE:</h3>
      <p>Lorem ipsum dolor sit amet, consectetuer adipiscing elit, sed diam nonummy nibh euismod tincidunt ut laoreet dolore magna aliquam erat volutpat. Ut wisi enim ad minim veniam, quis nostrud exerci tation ullamcorper</p>
    </div>
  </section>

  <section class="label label--two">
    <div class="signature" role="img" aria-label="Owner's handwritten signature"></div>
    <p class="website">www.vornematcha.com</p>
    <div class="badge-usda" role="img" aria-label="Organic certification badge"></div>
    <div class="badge-jas" role="img" aria-label="Japanese organic certification badge"></div>
    <div class="source-box">Sourced in<br>Uji, Japan<span class="map" role="img" aria-label="Outline map of Japan"></span></div>
    <p class="net-weight">NET WEIGHT: 30G</p>
    <p class="tagline-jp">生まれ変わった</p>
    <div class="title-block">
      <p class="brand-line">VORNE NO.7</p>
      <h1 class="product-name">MATCHA</h1>
      <div class="rule"></div>
      <p class="grade">CEREMONIAL GRADE</p>
    </div>
    <div class="info-box info-box--ingredients">
      <h3>INGREDIENTS:</h3>
      <p>Lorem ipsum dolor sit amet, consectetuer adipiscing elit, sed diam nonummy nibh euismod tincidunt ut laoreet dolore magna aliquam erat volutpat. Ut wisi</p>
    </div>
    <div class="info-box info-box--usage">
      <h3>HOW TO USE:</h3>
      <p>Lorem ipsum dolor sit amet, consectetuer adipiscing elit, sed diam nonummy nibh euismod tincidunt ut laoreet dolore magna aliquam erat volutpat. Ut wisi enim ad minim veniam, quis nostrud exerci tation ullamcorper</p>
    </div>
  </section>

  <section class="label label--three">
    <div class="signature" role="img" aria-label="Owner's handwritten signature"></div>
    <p class="website">www.vornematcha.com</p>
    <div class="badge-usda" role="img" aria-label="Organic certification badge"></div>
    <div class="badge-jas" role="img" aria-label="Japanese organic certification badge"></div>
    <div class="source-box">Sourced in<br>Uji, Japan<span class="map" role="img" aria-label="Outline map of Japan"></span></div>
    <p class="net-weight">NET WEIGHT: 30G</p>
    <p class="tagline-jp">生まれ変わった</p>
    <div class="title-block">
      <p class="brand-line">VORNE NO.7</p>
      <h1 class="product-name">MATCHA</h1>
      <div class="rule"></div>
      <p class="grade">CEREMONIAL GRADE</p>
    </div>
    <div class="info-box info-box--ingredients">
      <h3>INGREDIENTS:</h3>
      <p>Lorem ipsum dolor sit amet, consectetuer adipiscing elit, sed diam nonummy nibh euismod tincidunt ut laoreet dolore magna aliquam erat volutpat. Ut wisi</p>
    </div>
    <div class="info-box info-box--usage">
      <h3>HOW TO USE:</h3>
      <p>Lorem ipsum dolor sit amet, consectetuer adipiscing elit, sed diam nonummy nibh euismod tincidunt ut laoreet dolore magna aliquam erat volutpat. Ut wisi enim ad minim veniam, quis nostrud exerci tation ullamcorper</p>
    </div>
  </section>

</main>
</body>
</html>
```